Plakat für Hersteller von maßgefertigten Tischunikaten aus Massivholz
Zielgruppe
Wir sind einen Firma die sich auf die Fertigung von maßgefertigten Tischunikaten aus Massivholz spezialisiert hat. Unsere Zielgruppe sind Design affine Leute, im Alter von 35-55 Jahren
Aufgabenstellung
Wir benötigen das Design für eine Messewand mit den Maßen 443X227 cm. 5 Zentimeter rundlaufen dürfen keine Elemente mehr platziert werden. Die Messewand steht im Hintergrund von unserem Stand bei verschiedenen Designmessen
Infos die auf die Messewand müssen: Logo, Tischmanufaktur aus Stuttgart, Maßgefertigte Tischunikate (Bei der Formulierung bin ich flexibel, ihr könnt bspw. auch nur Stichworte benutzen, aber Stuttgart und maßgefertigt ist wichtig).
Die Messewand soll sehr minimalistisch gestaltet sein, bei der letzten Messewand hatten wir ein Foto von einem Tisch im Hintergrund und das sah merkwürdig aus.

```html
<!DOCTYPE html>
<html lang="de">
<head>
<meta charset="utf-8">
<title>Hollberg Manufaktur – Messewand</title>
<link href="https://fonts.googleapis.com/css2?family=Roboto:wght@300&family=Roboto+Slab:wght@700&display=swap" rel="stylesheet">
<style>
  :root {
    --wood-deep: #6e3515;
    --wood-mid: #a85d2c;
    --wood-warm: #c47a42;
    --wood-light: #dba06a;
    --text-light: #ffffff;
  }
  html, body {
    margin: 0;
    padding: 0;
    width: 1200px;
    height: 615px;
    overflow: hidden;
  }
  .trade-wall {
    position: relative;
    width: 1200px;
    height: 615px;
    overflow: hidden;
    background: var(--wood-mid);
  }
  .wood-surface {
    position: absolute;
    inset: 0;
    background:
      radial-gradient(ellipse 45% 22% at 62% 30%, rgba(219,160,106,0.75), transparent 70%),
      radial-gradient(ellipse 55% 25% at 45% 78%, rgba(219,160,106,0.6), transparent 70%),
      radial-gradient(ellipse 40% 30% at 8% 55%, rgba(110,53,21,0.55), transparent 70%),
      radial-gradient(ellipse 35% 40% at 95% 90%, rgba(110,53,21,0.6), transparent 70%),
      radial-gradient(ellipse 30% 20% at 20% 10%, rgba(110,53,21,0.5), transparent 70%),
      linear-gradient(170deg, var(--wood-warm) 0%, var(--wood-mid) 45%, var(--wood-warm) 70%, var(--wood-deep) 100%);
  }
  .brand {
    position: absolute;
    left: 62px;
    top: 41px;
    display: flex;
    align-items: center;
    gap: 20px;
  }
  .brand-dot {
    width: 90px;
    height: 90px;
    border: 3px solid var(--text-light);
    border-radius: 50%;
    box-sizing: border-box;
  }
  .brand-name {
    margin: 0;
    font-family: "Roboto Slab", Georgia, serif;
    font-weight: 700;
    font-size: 29px;
    line-height: 41px;
    color: var(--text-light);
  }
  .headline {
    position: absolute;
    left: 0;
    right: 0;
    top: 198px;
    margin: 0;
    text-align: center;
    font-family: "Roboto", Arial, sans-serif;
    font-weight: 300;
    font-size: 58px;
    line-height: 67px;
    color: var(--text-light);
  }
</style>
</head>
<body>
  <main class="trade-wall">
    <div class="wood-surface" role="img" aria-label="Nahaufnahme einer geschwungen geschnitzten Massivholzoberfläche mit Maserung und Rissen"></div>

    <header class="brand">
      <span class="brand-dot"></span>
      <p class="brand-name">Hollberg<br>Manufaktur</p>
    </header>

    <h1 class="headline">Maßgefertigte Tischunikate<br>aus Stuttgart</h1>
  </main>
</body>
</html>
```